Custom billboard campaign - Construction

We are starting a new billboard campaign and we need a design for our print billboards. We are a post-frame building company that builds custom buildings. We build homes, agricultural buildings, commercial buildings, and suburban/ hobby shops.
We would like to have our phone number (309)582-1936 as well as our website www.kestrovanframing.com
Text- Your post-frame experts!
Agriculture- Commercial - Homes - Suburban
Colors:
Black, chrome, white
We want our final design to be professional as well as luxurious/ high-end. I have attached our logo as well as building photos.
Construction - building

```html
<!DOCTYPE html>
<html lang="en">
<head>
<meta charset="utf-8">
<title>Kestrovan Framing – Billboard</title>
<link rel="stylesheet" href="https://fonts.googleapis.com/css2?family=Bebas+Neue&family=Poppins:wght@500;600;700&display=swap">
<style>
  :root {
    --ink: #231f20;
    --white: #ffffff;
    --chrome-light: #e6e6e6;
    --chrome-mid: #a7a7a7;
    --chrome-dark: #5e5e5e;
    --page: #ffffff;
  }
  * { margin: 0; padding: 0; box-sizing: border-box; }
  html, body { width: 922px; height: 1200px; overflow: hidden; background: var(--page); }
  .billboard {
    position: absolute; left: 41px; top: 495px;
    width: 840px; height: 210px;
    background: var(--white);
    box-shadow: 0 2px 6px rgba(0,0,0,.25);
    font-family: "Poppins", sans-serif;
    overflow: hidden;
  }
  .billboard svg.shapes { position: absolute; inset: 0; }
  .brand-name {
    position: absolute; left: 0; width: 275px; top: 14px;
    text-align: center; color: var(--ink);
    font-family: "Poppins", sans-serif; font-weight: 700;
    line-height: 1;
  }
  .brand-name .main { display: block; font-size: 34px; letter-spacing: 1px; }
  .brand-name .sub { display: block; font-size: 14px; letter-spacing: 3px; margin-top: 8px; }
  .phone {
    position: absolute; left: 30px; top: 137px;
    display: flex; align-items: center; gap: 9px;
    color: var(--white); font-weight: 600; font-size: 27px; letter-spacing: .5px;
  }
  .phone svg { width: 20px; height: 20px; }
  .headline {
    position: absolute; left: 596px; top: 22px;
    color: var(--white);
    font-family: "Bebas Neue", sans-serif; font-size: 39px; line-height: 34px;
    letter-spacing: .5px;
  }
  .services {
    position: absolute; left: 596px; top: 106px;
    display: grid; grid-template-columns: 126px auto; row-gap: 1px;
    list-style: none; color: var(--ink); font-weight: 600; font-size: 14.5px; line-height: 19px;
  }
  .services li { display: flex; align-items: center; gap: 5px; }
  .services svg { width: 11px; height: 11px; flex: none; }
  .website {
    position: absolute; left: 572px; width: 262px; top: 158px;
    text-align: center; color: var(--white); font-weight: 500; font-size: 16.5px;
  }
</style>
</head>
<body>
  <div class="billboard">
    <svg class="shapes" width="840" height="210" viewBox="0 0 840 210">
      <defs>
        <linearGradient id="chrome" x1="0" y1="0" x2="1" y2="1">
          <stop offset="0" stop-color="var(--chrome-dark)"/>
          <stop offset=".5" stop-color="var(--chrome-light)"/>
          <stop offset="1" stop-color="var(--chrome-mid)"/>
        </linearGradient>
        <linearGradient id="photoTones" x1="0" y1="0" x2="0" y2="1">
          <stop offset="0" stop-color="#a9b9cf"/>
          <stop offset=".3" stop-color="#8c4a4f"/>
          <stop offset=".6" stop-color="#9a3a3e"/>
          <stop offset=".78" stop-color="#5d6b44"/>
          <stop offset="1" stop-color="#a8a296"/>
        </linearGradient>
        <linearGradient id="webBand" x1="0" y1="0" x2="1" y2="0">
          <stop offset="0" stop-color="var(--ink)"/>
          <stop offset=".55" stop-color="#3a3839"/>
          <stop offset="1" stop-color="#6a6a6a"/>
        </linearGradient>
      </defs>
      <polygon class="chrome-edge" points="250,0 262,0 250,210 237,210" fill="url(#chrome)"/>
      <polygon class="photo" role="img" aria-label="Photo of a red steel post-frame building with landscaped gravel garden" points="260,0 548,0 566,210 248,210" fill="url(#photoTones)"/>
      <polygon class="chrome-edge" points="540,0 556,0 600,210 584,210" fill="url(#chrome)"/>
      <polygon class="headline-panel" points="554,0 840,0 840,103 574,103" fill="var(--ink)"/>
      <polygon class="service-panel" points="574,103 840,103 840,210 596,210" fill="var(--white)"/>
      <polygon class="web-band" points="538,151 840,151 840,186 531,186" fill="url(#webBand)"/>
      <polygon class="phone-band" points="0,124 300,124 285,186 0,186" fill="var(--ink)"/>
    </svg>

    <div class="brand-name">
      <span class="main">KESTROVAN</span>
      <span class="sub">FRAMING, INC.</span>
    </div>

    <div class="phone">
      <svg viewBox="0 0 24 24" aria-hidden="true"><path fill="var(--white)" d="M6.6 10.8a15.1 15.1 0 0 0 6.6 6.6l2.2-2.2a1 1 0 0 1 1-.25 11.4 11.4 0 0 0 3.6.57 1 1 0 0 1 1 1V20a1 1 0 0 1-1 1A17 17 0 0 1 3 4a1 1 0 0 1 1-1h3.5a1 1 0 0 1 1 1 11.4 11.4 0 0 0 .57 3.6 1 1 0 0 1-.25 1z"/></svg>
      <span>(309)582-1936</span>
    </div>

    <h1 class="headline">YOUR POST-FRAME<br>EXPERTS!</h1>

    <ul class="services">
      <li><svg viewBox="0 0 12 12"><circle cx="6" cy="6" r="6" fill="var(--ink)"/><path d="M3.2 6.2l1.8 1.8 3.8-3.8" stroke="var(--white)" stroke-width="1.6" fill="none"/></svg>Agriculture</li>
      <li><svg viewBox="0 0 12 12"><circle cx="6" cy="6" r="6" fill="var(--ink)"/><path d="M3.2 6.2l1.8 1.8 3.8-3.8" stroke="var(--white)" stroke-width="1.6" fill="none"/></svg>Homes</li>
      <li><svg viewBox="0 0 12 12"><circle cx="6" cy="6" r="6" fill="var(--ink)"/><path d="M3.2 6.2l1.8 1.8 3.8-3.8" stroke="var(--white)" stroke-width="1.6" fill="none"/></svg>Commercial</li>
      <li><svg viewBox="0 0 12 12"><circle cx="6" cy="6" r="6" fill="var(--ink)"/><path d="M3.2 6.2l1.8 1.8 3.8-3.8" stroke="var(--white)" stroke-width="1.6" fill="none"/></svg>Suburban</li>
    </ul>

    <div class="website">www.kestrovanframing.com</div>
  </div>
</body>
</html>
```